BRANDEMEIER & BRANDEMEIER,LLP NEEDS A NEW LETTERHEAD DESIGN

a conservative yet contemporary layout befitting a long established
firm, consistent with the times, some form of logo so it catches ones attention, and is
admirable, but portrays integrity
Updates

I would like to approve #22066987 Please advise how to do this as it’s confusing on the site so I can approve payment for the designer

Target Market(s)

real estate investors and building management people

Industry/Entity Type

Law Firm

Font styles to use
Serif

Colors

Designer to choose colors to be used in the design.

Requirements
Must have
• some form of conservative logo

```html
<!DOCTYPE html>
<html lang="en">
<head>
<meta charset="utf-8">
<title>Brandemeier &amp; Brandemeier LLP Letterhead</title>
<link href="https://fonts.googleapis.com/css2?family=Cinzel:wght@500&family=Roboto:wght@300;400&display=swap" rel="stylesheet">
<style>
  :root {
    --backdrop: #c9cad0;
    --paper: #f2f2f2;
    --ink: #4a4a4a;
    --ink-soft: #5a5a5a;
    --gold: #d9a73a;
    --rule: #9a9a9a;
  }
  * { margin: 0; padding: 0; box-sizing: border-box; }
  html, body {
    width: 1200px; height: 1166px; overflow: hidden;
    background: var(--backdrop);
  }
  .letterhead {
    position: absolute; left: 160px; top: 15px;
    width: 880px; height: 1136px;
    background: var(--paper);
    box-shadow: 0 2px 6px rgba(0,0,0,0.25);
    font-family: "Roboto", Arial, sans-serif;
    font-weight: 300;
    color: var(--ink-soft);
  }
  .brand {
    position: absolute; left: 79px; top: 64px;
    display: flex; align-items: center; gap: 18px;
  }
  .brand-mark { width: 64px; height: 64px; }
  .brand-name {
    font-family: "Cinzel", Georgia, serif;
    font-weight: 500; font-size: 22px; letter-spacing: 0.3px;
    color: var(--ink);
    padding-bottom: 5px;
    border-bottom: 1px solid var(--rule);
  }
  .brand-tagline {
    font-family: "Cinzel", Georgia, serif;
    font-weight: 500; font-size: 10.5px; letter-spacing: 5.2px;
    color: var(--ink); margin-top: 7px;
  }
  .recipient {
    position: absolute; left: 79px; top: 275px;
    font-size: 12.5px; line-height: 15.3px;
  }
  .letter-body {
    position: absolute; left: 79px; top: 404px; width: 723px;
    font-size: 12.2px; line-height: 15.3px;
  }
  .letter-body p { text-align: justify; margin-bottom: 15px; }
  .letter-body .salutation { margin-bottom: 15px; }
  .closing {
    position: absolute; left: 79px; top: 858px;
    font-size: 12.5px; line-height: 15.3px;
  }
  .signature {
    width: 145px; height: 60px; margin: 18px 0 18px;
    background: linear-gradient(90deg, rgba(20,20,20,0.08), rgba(20,20,20,0.18), rgba(20,20,20,0.06));
    border-radius: 30px;
  }
  .footer {
    position: absolute; left: 79px; top: 1155px; top: 1100px; width: 723px;
    font-size: 11.6px; text-align: center; white-space: nowrap;
  }
  .footer .label { color: var(--gold); }
</style>
</head>
<body>
  <main class="letterhead">
    <header class="brand">
      <svg class="brand-mark" viewBox="0 0 64 64" aria-hidden="true">
        <circle cx="32" cy="32" r="29" fill="none" stroke="var(--gold)" stroke-width="2"/>
      </svg>
      <div>
        <div class="brand-name">BRANDEMEIER &amp; BRANDEMEIER LLP</div>
        <div class="brand-tagline">ATTORNEYS AND COUNSELORS AT LAW</div>
      </div>
    </header>

    <address class="recipient" style="font-style:normal">
      Mr. Laurent Whitcombe<br>
      President and CEO<br>
      Veridian Labs LLC.<br>
      880 Hudson Avenue, Suite 2100<br>
      New York, NY 10027
    </address>

    <section class="letter-body">
      <p class="salutation">Dear Mr. Whitcombe:</p>
      <p>As Chairperson of the Corporate Conscience Campaign - Helping the Homeless in New York, I am writing this to thank you personally for your company's support in last month's fund-raising effort.</p>
      <p>As I indicated when we spoke on the phone two weeks ago, the campaign was considered a resounding success, raising a total of $1.65 million to-date, significantly exceeding our target of $1 million. Some donations are still trickling in, so we could end up close to a total of $2 million.</p>
      <p>Veridian Labs was an influential leader throughout the entire three-month campaign. In fact, we couldn't have succeeded without the generous support of your company, both financially, and through your organizational and administrative assistance. Your Team Leader, Marianne Holloway was particularly impressive, going above and beyond what we could have expected of someone performing as a volunteer while continuing on with her day-to-day duties. Please convey my special thanks to Marianne.</p>
      <p>I would also ask you to convey my sincere thanks and congratulations to all of those other people in your company who contributed in any way to the Helping the Homeless Campaign. Please tell them that the sum of their contributions resulted in a major success that they should all be proud of taking part in.</p>
      <p>I believe that the 27 companies that participated in this effort have set a new standard for social responsibility in this community, and have set a powerful example that will inspire other companies and organizations to do the same.</p>
      <p>I look forward to seeing you at the Mayor's special thank you reception next month.</p>
    </section>

    <section class="closing">
      <div>Yours sincerely,</div>
      <div class="signature" role="img" aria-label="Handwritten signature of the fundraising chair"></div>
      <div>Gerald Ashworth<br>Fundraising Chair</div>
    </section>

    <footer class="footer">
      48 Carroll Street Suite 210, Brooklyn, New York 11231 · <span class="label">T:</span> (718)-555-0142 · <span class="label">F:</span> (718)-555-0187 · <span class="label">E:</span> info@brandemeierlaw.com · <span class="label">W:</span> www.brandemeierlaw.com
    </footer>
  </main>
</body>
</html>
```